Wandering Rooms Stationary Set

Wandering Rooms is a bespoke interior design firm set to provide services to VIP clients with elegance and minimalism is the main theme for our stationary set. We require a full stationary set covering A4 letterhead, A4 & A3 envelopes, business cards, USB's, CDs, email signature and any other item the designer sees fit. logo is already designed and finalized, and we require the designer to use it as is without modifying the logo.

Address to be used on letterhead / business cards ...etc shall be as follows:

Phone : +971 2 518 2047
P.O. Box : 309186
Address: Block C&D, Bldg. 47, Court 12, Abu Dhabi, United Arab Emirates
Website: www.wanderingrooms-example.com

Target Market(s)

VIP Clients

Industry/Entity Type

Interior Design

Font styles to use
Other font styles liked:
• something to be unique

Colors

Designer to choose colors to be used in the design.

Requirements
Must have
• Elegant, minimalistic
Nice to have
• Simple yet elegant design having a sharp yet clean cut format
Should not have
• No additional colours, just colours that are used in the logo (silver, black or gold)

```html
<!DOCTYPE html>
<html lang="en">
<head>
<meta charset="utf-8">
<title>Wandering Rooms – Business Card</title>
<link rel="stylesheet" href="https://fonts.googleapis.com/css2?family=Cormorant+Garamond:wght@400;500&family=Crimson+Text&family=Allura&display=swap">
<style>
  :root {
    --backdrop: #151515;
    --card-black: #2a2a2a;
    --card-white: #ffffff;
    --silver: #cfcfcf;
    --gold: #a88a4e;
    --ink: #3a3a3a;
  }
  * { margin: 0; padding: 0; box-sizing: border-box; }
  html, body {
    width: 1200px; height: 800px; overflow: hidden;
    background: var(--backdrop);
  }
  .canvas {
    width: 1200px; height: 800px;
    display: flex; align-items: center; justify-content: center; gap: 40px;
  }
  .card {
    width: 520px; height: 298px;
    border-radius: 18px;
    position: relative;
    overflow: hidden;
  }
  .card--front {
    background: var(--card-black);
    display: flex; align-items: center; justify-content: center;
  }
  .card--back {
    background: var(--card-white);
    border-bottom: 5px solid var(--gold);
  }
  .brand-name {
    font-family: "Cormorant Garamond", serif;
    font-weight: 400;
    letter-spacing: 0.14em;
    text-transform: uppercase;
  }
  .card--front .brand-name {
    color: var(--silver);
    font-size: 34px;
  }
  .card--back .brand-name {
    position: absolute; left: 40px; top: 52px;
    color: var(--gold);
    font-size: 26px;
  }
  .holder {
    position: absolute; left: 44px; bottom: 34px;
  }
  .holder__name {
    font-family: "Allura", cursive;
    color: var(--gold);
    font-size: 32px; line-height: 1;
  }
  .holder__role {
    font-family: "Crimson Text", serif;
    color: var(--ink);
    font-size: 15px;
  }
  .contact {
    position: absolute; right: 34px; top: 118px;
    font-family: "Crimson Text", serif;
    color: var(--ink);
    font-size: 11.5px; line-height: 1.35;
  }
  .contact__address { margin-bottom: 10px; }
  .contact__line { display: flex; align-items: center; gap: 7px; }
  .contact__icon { width: 9px; height: 9px; flex: none; fill: var(--gold); }
</style>
</head>
<body>
<main class="canvas">
  <section class="card card--front">
    <p class="brand-name">Wandering Rooms</p>
  </section>

  <section class="card card--back">
    <p class="brand-name">Wandering Rooms</p>

    <div class="holder">
      <p class="holder__name">Daniel Hartley</p>
      <p class="holder__role">President</p>
    </div>

    <div class="contact">
      <p class="contact__address">P.O. Box : 309186,<br>Block C&amp;D, Bldg. 47, Court 12<br>Abu Dhabi, United Arab Emirate</p>
      <p class="contact__line">
        <svg class="contact__icon" viewBox="0 0 10 10" aria-hidden="true"><path d="M2 0.5 L3.6 2.6 L2.7 3.6 Q3.6 5.6 6.4 7.3 L7.4 6.4 L9.5 8 L8.3 9.5 Q4.5 9.4 0.5 1.7 Z"/></svg>
        +971 2 518 2047
      </p>
      <p class="contact__line">
        <svg class="contact__icon" viewBox="0 0 10 10" aria-hidden="true"><path d="M0 2 H10 V8.5 H0 Z M0.8 2.6 L5 5.6 L9.2 2.6" stroke="#fff" stroke-width="0.8"/></svg>
        info@wanderingrooms-example.com
      </p>
      <p class="contact__line">
        <svg class="contact__icon" viewBox="0 0 10 10" aria-hidden="true"><circle cx="5" cy="5" r="4.6"/><path d="M0.6 5 H9.4 M5 0.4 Q2.6 5 5 9.6 M5 0.4 Q7.4 5 5 9.6" stroke="#fff" stroke-width="0.6" fill="none"/></svg>
        www.wanderingrooms-example.com
      </p>
    </div>
  </section>
</main>
</body>
</html>
```